Business Card for Vorla Parts Wholesale supplier

Hi There! I need a new business card for our company. We are specialized in selling Vorla parts, mostly we sell new LCD screens for Zelnar and Drelks. I would like to see that back in the design.

You can find the colors and logo's on our website: www.hartuvo.nl

Industry/Entity Type

Business

Contact Information for Business Card

My Details:
Tobias Lindqvist

Phone: 0031687203316
E-mail: Tobias@hartuvo.nl

Slogan: "Because Quality Matters"

Font styles to use
Sans Serif

Colors

Designer to choose colors to be used in the design.

Requirements
Must have
• A Black backside with the Hartuvo logo on it. The front side should be clean with only my contact details.
• But I'm also open for something really different or awesome!
Nice to have
• Remember that we are in the parts & repairing industry, So i'll be handing those business cards mainly to repair companies. Maybe you can do something with that thought :)

```html
<!DOCTYPE html>
<html lang="en">
<head>
<meta charset="utf-8">
<title>Hartuvo Business Card</title>
<link rel="stylesheet" href="https://fonts.googleapis.com/css2?family=Arimo:ital,wght@0,400;0,700;1,400&display=swap">
<style>
  :root {
    --ink: #141414;
    --card-black: #1a1a1a;
    --orange: #f2561d;
    --orange-deep: #d9470f;
    --white: #ffffff;
    --backdrop: #e7e3dc;
    --card-w: 860px;
    --card-h: 506px;
  }
  * { box-sizing: border-box; margin: 0; padding: 0; }
  html, body {
    width: 1200px; height: 1200px; overflow: hidden;
    background: var(--backdrop);
    font-family: "Arimo", Arial, sans-serif;
  }
  .sheet {
    width: 1200px; height: 1200px;
    display: flex; flex-direction: column; align-items: center;
    justify-content: center; gap: 60px;
  }
  .card {
    position: relative;
    width: var(--card-w); height: var(--card-h);
    overflow: hidden;
    box-shadow: 0 10px 28px rgba(0,0,0,.18);
  }

  /* Back side */
  .card--back { background: var(--card-black); }
  .card--back .brand {
    position: absolute; left: 50%; top: 170px; transform: translateX(-50%);
    display: flex; align-items: center; gap: 26px;
  }
  .brand__dot {
    width: 96px; height: 96px; border-radius: 50%;
    background: var(--orange);
  }
  .brand__name {
    font-weight: 700; font-size: 104px; line-height: 1;
    letter-spacing: 2px; color: var(--white);
  }
  .card--back .tagline {
    position: absolute; right: 118px; top: 300px;
    color: var(--orange); font-size: 30px; letter-spacing: .5px;
  }
  .card--back .edge-band {
    position: absolute; left: 0; right: 0; bottom: 0; height: 38px;
    background: var(--orange);
  }

  /* Front side */
  .card--front { background: var(--orange); }
  .card--front .brand {
    position: absolute; right: 66px; top: 52px;
    display: flex; align-items: center; gap: 16px;
  }
  .card--front .brand__dot { width: 58px; height: 58px; background: var(--ink); }
  .card--front .brand__name { font-size: 62px; color: var(--white); letter-spacing: 1px; }
  .card--front .tagline {
    position: absolute; right: 66px; top: 130px;
    font-style: italic; font-size: 20px; color: var(--ink);
  }
  .contact {
    position: absolute; left: 66px; bottom: 92px;
    display: flex; align-items: center; gap: 26px;
  }
  .contact__name {
    font-weight: 700; font-size: 34px; letter-spacing: .5px;
    text-transform: uppercase; color: var(--ink);
  }
  .contact__divider { width: 2px; height: 92px; background: var(--ink); }
  .contact__list { list-style: none; display: flex; flex-direction: column; gap: 16px; }
  .contact__item {
    display: flex; align-items: center; gap: 16px;
    font-size: 22px; color: var(--ink);
  }
  .contact__icon { width: 30px; height: 30px; flex: none; }
  .card--front .edge-band {
    position: absolute; left: 0; right: 0; bottom: 0; height: 30px;
    background: var(--ink);
  }
</style>
</head>
<body>
<main class="sheet">

  <section class="card card--back" aria-label="Business card back">
    <div class="brand">
      <span class="brand__dot"></span>
      <span class="brand__name">hartuvo</span>
    </div>
    <p class="tagline">"Because Quality Matters"</p>
    <div class="edge-band"></div>
  </section>

  <section class="card card--front" aria-label="Business card front">
    <div class="brand">
      <span class="brand__dot"></span>
      <span class="brand__name">hartuvo</span>
    </div>
    <p class="tagline">"Because Quality Matters"</p>

    <div class="contact">
      <p class="contact__name">Tobias Lindqvist</p>
      <span class="contact__divider"></span>
      <ul class="contact__list">
        <li class="contact__item">
          <svg class="contact__icon" viewBox="0 0 30 30" aria-hidden="true">
            <circle cx="15" cy="15" r="15" fill="#141414"/>
            <path d="M10.5 8.5c.8-.6 1.7-.4 2.1.4l1.2 2.3c.3.6.1 1.3-.4 1.7l-1 .7c.7 1.7 2 3.1 3.7 3.9l.8-.9c.5-.5 1.2-.6 1.8-.3l2.2 1.3c.8.5.9 1.4.3 2.1l-1 1.1c-.8.8-2 1-3 .6-4.1-1.6-7-4.8-8.2-8.9-.3-1.1 0-2.2.8-2.9z" fill="#f2561d"/>
          </svg>
          <span>0031687203316</span>
        </li>
        <li class="contact__item">
          <svg class="contact__icon" viewBox="0 0 30 30" aria-hidden="true">
            <circle cx="15" cy="15" r="15" fill="#141414"/>
            <rect x="8" y="10" width="14" height="10" fill="none" stroke="#f2561d" stroke-width="1.6"/>
            <path d="M8 10l7 6 7-6" fill="none" stroke="#f2561d" stroke-width="1.6"/>
          </svg>
          <span>Tobias@hartuvo.nl</span>
        </li>
      </ul>
    </div>
    <div class="edge-band"></div>
  </section>

</main>
</body>
</html>
```